Need Business Card for our Real Estate Business with Sales Executive's Picture

PANTONE 484 C ( RED)

PANTONE 2766 C ( BLUE

Industry/Entity Type

Real Estate

Contact Information for Business Card

Name, Mobile, email, & picture of Person
Agency Phone, address, Web address

Requirements
Must have
• Our Logo Colours, Agent Picture,

```html
<!DOCTYPE html>
<html lang="en">
<head>
<meta charset="utf-8">
<title>Dunmore Real Estate – Business Card</title>
<link rel="stylesheet" href="https://fonts.googleapis.com/css2?family=Lato:wght@400;700&display=swap">
<style>
  :root {
    --navy: #262a45;
    --navy-deep: #1f2239;
    --red: #7b2430;
    --white: #ffffff;
    --ink: #1c1c24;
    --backdrop: #3a3a3c;
    --photo-top: #e9ecf3;
    --photo-bottom: #2f4a8a;
  }
  * { box-sizing: border-box; margin: 0; padding: 0; }
  html, body { width: 1200px; height: 900px; overflow: hidden; }
  body {
    background: var(--backdrop);
    font-family: "Lato", sans-serif;
    position: relative;
  }
  .card {
    position: absolute;
    width: 600px;
    height: 343px;
    overflow: hidden;
    border-radius: 3px;
  }
  /* Back side */
  .card-back {
    left: 80px; top: 70px;
    background: var(--navy);
    color: var(--white);
    display: flex; flex-direction: column; align-items: center; justify-content: center;
  }
  .brand-mark {
    display: flex; align-items: center; gap: 12px;
    font-weight: 400;
    letter-spacing: 4px;
    text-transform: uppercase;
  }
  .brand-mark .brand-square { width: 12px; height: 12px; background: currentColor; }
  .card-back .brand-mark { font-size: 34px; }
  .card-back .rule { width: 300px; height: 1px; background: var(--white); margin: 18px 0 22px; opacity: .8; }
  .card-back .web { font-size: 17px; letter-spacing: .5px; }

  /* Front side */
  .card-front {
    left: 520px; top: 470px;
    background: var(--white);
    color: var(--ink);
  }
  .agent-photo {
    position: absolute; left: 40px; top: 60px; width: 290px; height: 283px;
    background: linear-gradient(180deg, var(--photo-top) 0%, var(--photo-bottom) 100%);
  }
  .card-band { position: absolute; left: 0; top: 0; width: 600px; height: 343px; }
  .details {
    position: absolute; right: 30px; top: 26px;
    text-align: right;
  }
  .card-front .brand-mark {
    font-size: 22px; color: var(--navy); justify-content: flex-end;
  }
  .agent-name { margin-top: 22px; font-size: 22px; font-weight: 700; color: var(--red); }
  .agent-title { font-size: 14px; margin-top: 2px; }
  .contact-list { list-style: none; margin-top: 10px; font-size: 14px; line-height: 1.45; }
  .contact-list li { display: flex; justify-content: flex-end; align-items: center; gap: 8px; }
  .contact-list svg { width: 13px; height: 13px; fill: var(--red); }
  .card-front .web {
    position: absolute; left: 150px; bottom: 16px;
    color: var(--white); font-size: 15px; letter-spacing: .3px;
  }
</style>
</head>
<body>

  <section class="card card-back">
    <div class="brand-mark"><span class="brand-square"></span>Dunmore Real Estate</div>
    <div class="rule"></div>
    <div class="web">www.dunmorerealty.com</div>
  </section>

  <section class="card card-front">
    <div class="agent-photo" role="img" aria-label="Portrait photo of the sales manager in a blue suit"></div>

    <svg class="card-band" viewBox="0 0 600 343" aria-hidden="true">
      <path d="M0,300 Q300,280 600,210 L600,343 L0,343 Z" fill="var(--red)"/>
      <path d="M0,312 Q300,292 600,224 L600,343 L0,343 Z" fill="var(--white)"/>
      <path d="M0,318 Q300,298 600,232 L600,343 L0,343 Z" fill="var(--navy)"/>
    </svg>

    <div class="details">
      <div class="brand-mark"><span class="brand-square"></span>Dunmore Real Estate</div>
      <div class="agent-name">Daniel Ashford</div>
      <div class="agent-title">Manager</div>
      <ul class="contact-list">
        <li>555 010 2400
          <svg viewBox="0 0 24 24"><path d="M6.6 10.8a15 15 0 0 0 6.6 6.6l2.2-2.2a1 1 0 0 1 1-.25 11.4 11.4 0 0 0 3.6.57 1 1 0 0 1 1 1V20a1 1 0 0 1-1 1A17 17 0 0 1 3 4a1 1 0 0 1 1-1h3.5a1 1 0 0 1 1 1c0 1.25.2 2.45.57 3.57a1 1 0 0 1-.25 1z"/></svg></li>
        <li>555 010 2401
          <svg viewBox="0 0 24 24"><path d="M7 1h10a2 2 0 0 1 2 2v18a2 2 0 0 1-2 2H7a2 2 0 0 1-2-2V3a2 2 0 0 1 2-2zm0 3v14h10V4zm5 15.5a1 1 0 1 0 0 2 1 1 0 0 0 0-2z"/></svg></li>
        <li>info@dunmorerealty.com
          <svg viewBox="0 0 24 24"><path d="M2 5h20v14H2zm2 2v.5l8 5 8-5V7zm0 3v7h16v-7l-8 5z"/></svg></li>
        <li>48 Cedar Row, Fairview, TX 75000</li>
      </ul>
    </div>

    <div class="web">www.dunmorerealty.com</div>
  </section>

</body>
</html>
```